Residential Remodeling Contractor needs updated business card

I need a new design for my business card.
Name of the company is Ridgefell Construction. I need a card that commands presence, strength, integrity. I have been in business for 28 years. I am a Residential Remodeling Contractor that covers all aspects of a residential remodel and build.

```html
<!DOCTYPE html>
<html lang="en">
<head>
<meta charset="utf-8">
<title>Ridgefell Construction – Business Card</title>
<link rel="stylesheet" href="https://fonts.googleapis.com/css2?family=Montserrat:wght@400;500;700&display=swap">
<style>
  :root {
    --navy: #1f3d7f;
    --navy-text: #1d3a7c;
    --paper: #ffffff;
    --ink: #1c1c1c;
    --stage: #e4e4e7;
    --shadow: rgba(0, 0, 0, 0.18);
  }
  * { box-sizing: border-box; margin: 0; padding: 0; }
  html, body {
    width: 1200px;
    height: 786px;
    overflow: hidden;
    background: var(--stage);
    font-family: "Montserrat", Arial, sans-serif;
  }
  .sheet {
    position: relative;
    width: 1200px;
    height: 786px;
    display: flex;
    align-items: center;
    justify-content: center;
    gap: 50px;
  }
  .card {
    position: relative;
    width: 540px;
    height: 310px;
    overflow: hidden;
    box-shadow: 0 10px 28px var(--shadow);
  }
  /* Front */
  .card--front { background: var(--paper); }
  .card__band {
    position: absolute;
    inset: 0;
    background: var(--navy);
    clip-path: polygon(38% 0, 100% 0, 100% 100%, 71% 100%);
  }
  .card__wordmark {
    position: absolute;
    display: flex;
    align-items: center;
    gap: 10px;
    color: var(--paper);
    font-weight: 500;
    text-transform: uppercase;
    letter-spacing: 0.06em;
    line-height: 1.15;
  }
  .card__wordmark-square {
    width: 12px;
    height: 12px;
    background: var(--paper);
    flex: none;
  }
  .card--front .card__wordmark {
    left: 330px;
    top: 92px;
    font-size: 17px;
  }
  .person {
    position: absolute;
    left: 40px;
    top: 84px;
  }
  .person__name {
    color: var(--navy-text);
    font-weight: 700;
    font-size: 21px;
  }
  .person__role {
    color: var(--ink);
    font-size: 11px;
    margin-top: 4px;
    margin-left: 8px;
  }
  .address {
    position: absolute;
    left: 50px;
    top: 160px;
    color: var(--ink);
    font-size: 12px;
    line-height: 1.3;
  }
  .contacts {
    position: absolute;
    left: 50px;
    top: 214px;
    list-style: none;
  }
  .contacts__item {
    display: flex;
    align-items: center;
    gap: 12px;
    color: var(--ink);
    font-size: 12px;
    height: 22px;
  }
  .contacts__icon {
    width: 14px;
    height: 14px;
    fill: var(--navy-text);
    flex: none;
  }
  /* Back */
  .card--back { background: var(--navy); }
  .card--back .card__wordmark {
    left: 50%;
    top: 50%;
    transform: translate(-50%, -50%);
    font-size: 24px;
    gap: 14px;
  }
  .card--back .card__wordmark-square { width: 16px; height: 16px; }
</style>
</head>
<body>
<main class="sheet">
  <section class="card card--front" aria-label="Business card front">
    <div class="card__band"></div>
    <div class="card__wordmark">
      <span class="card__wordmark-square"></span>
      <span>Ridgefell<br>Construction</span>
    </div>
    <div class="person">
      <p class="person__name">Dana Whitlock</p>
      <p class="person__role">Owner</p>
    </div>
    <p class="address">48 Cedar Hollow Lane<br>Brandon, MS 39047</p>
    <ul class="contacts">
      <li class="contacts__item">
        <svg class="contacts__icon" viewBox="0 0 16 16" aria-hidden="true"><path d="M3 1h3l1.5 3.5-2 1.3a9 9 0 0 0 4.7 4.7l1.3-2L15 10v3a2 2 0 0 1-2 2A12 12 0 0 1 1 3a2 2 0 0 1 2-2z"/></svg>
        <span>555.014.2273</span>
      </li>
      <li class="contacts__item">
        <svg class="contacts__icon" viewBox="0 0 16 16" aria-hidden="true"><path d="M1 3h14v10H1z M1 3l7 6 7-6" fill="none" stroke="#1d3a7c" stroke-width="1.6"/></svg>
        <span>info@ridgefellconstruction.com</span>
      </li>
      <li class="contacts__item">
        <svg class="contacts__icon" viewBox="0 0 16 16" aria-hidden="true"><g fill="none" stroke="#1d3a7c" stroke-width="1.4"><circle cx="8" cy="8" r="6.5"/><ellipse cx="8" cy="8" rx="2.8" ry="6.5"/><path d="M1.5 8h13"/></g></svg>
        <span>www.ridgefellconstruction.com</span>
      </li>
    </ul>
  </section>

  <section class="card card--back" aria-label="Business card back">
    <div class="card__wordmark">
      <span class="card__wordmark-square"></span>
      <span>Ridgefell<br>Construction</span>
    </div>
  </section>
</main>
</body>
</html>
```